Business Card Design for Occupational Medicine Start Up Company

We need to design a professional business card. We are a healthcare company providing occupational medicine services to blue collar industries. We are professional, efficient and high quality service providers.

Target Market(s)

Blue Collar Industry: Shipbuilding, Ports, Trucking Companies; The Executives and Safety Officers for these companies

Industry/Entity Type

Healthcare

Contact Information for Business Card

Logo, Name, Title, Email, Phone

Other font styles liked:
• Please match our Brand Guide

Requirements
Must have
• Our Company Colors and Logo

```html
<!DOCTYPE html>
<html lang="en">
<head>
<meta charset="utf-8">
<title>Crewline Health – Business Card</title>
<link rel="stylesheet" href="https://fonts.googleapis.com/css2?family=Montserrat:wght@300;700&family=Arimo:wght@400&display=swap">
<style>
  :root {
    --page: #2b2b2d;
    --card: #0c0c0d;
    --brand-blue: #2f3c9c;
    --sky-blue: #1e9ad6;
    --gold: #e9a43a;
    --white: #f3f3f3;
    --silver: #cfcfd2;
    --rule: #5a5a5e;
  }
  * { margin: 0; padding: 0; box-sizing: border-box; }
  html, body { width: 1200px; height: 900px; overflow: hidden; }
  body {
    background: var(--page);
    display: flex;
    align-items: center;
    justify-content: center;
    gap: 40px;
  }
  .card {
    width: 540px;
    height: 309px;
    background: var(--card);
    border-radius: 22px;
    position: relative;
  }

  /* Front */
  .card--front { display: flex; align-items: center; }
  .front__brand {
    width: 50%;
    height: 100%;
    display: flex;
    align-items: center;
    justify-content: center;
    gap: 10px;
  }
  .brand-dot {
    width: 18px; height: 18px;
    border-radius: 50%;
    background: var(--brand-blue);
    flex: none;
  }
  .brand-name {
    font-family: "Montserrat", sans-serif;
    font-weight: 700;
    font-size: 21px;
    letter-spacing: 0.5px;
    color: var(--brand-blue);
    white-space: nowrap;
  }
  .front__divider {
    width: 1px;
    height: 140px;
    background: var(--rule);
  }
  .front__contact {
    padding-left: 26px;
    font-family: "Arimo", sans-serif;
    color: var(--white);
  }
  .person__name {
    font-family: "Montserrat", sans-serif;
    font-size: 19px;
    color: var(--gold);
    letter-spacing: 0.3px;
  }
  .person__first { font-weight: 700; }
  .person__last { font-weight: 300; }
  .person__title { font-size: 14px; margin-bottom: 14px; }
  .contact-list { list-style: none; font-size: 13px; line-height: 1.55; }
  .contact-list li { display: flex; align-items: center; gap: 8px; }
  .contact-icon { width: 13px; height: 13px; flex: none; }
  .web-highlight { color: var(--sky-blue); }

  /* Back */
  .card--back {
    display: flex;
    align-items: center;
    justify-content: center;
    gap: 12px;
  }
  .card--back .brand-dot { width: 22px; height: 22px; background: var(--silver); }
  .card--back .brand-name { font-size: 28px; color: var(--silver); }
</style>
</head>
<body>

<section class="card card--front" aria-label="Business card front">
  <div class="front__brand">
    <span class="brand-dot"></span>
    <span class="brand-name">CREWLINE HEALTH</span>
  </div>
  <div class="front__divider"></div>
  <div class="front__contact">
    <p class="person__name"><span class="person__first">DANIEL</span> <span class="person__last">REYES</span></p>
    <p class="person__title">Managing Director</p>
    <ul class="contact-list">
      <li>
        <svg class="contact-icon" viewBox="0 0 24 24" aria-hidden="true"><path fill="#e9a43a" d="M6.6 10.8a15.1 15.1 0 0 0 6.6 6.6l2.2-2.2c.3-.3.7-.4 1-.2 1.1.4 2.3.6 3.6.6.6 0 1 .4 1 1V20c0 .6-.4 1-1 1A17 17 0 0 1 3 4c0-.6.4-1 1-1h3.5c.6 0 1 .4 1 1 0 1.3.2 2.5.6 3.6.1.3 0 .7-.2 1z"/></svg>
        044-210 738 615
      </li>
      <li>
        <svg class="contact-icon" viewBox="0 0 24 24" aria-hidden="true"><rect x="2" y="5" width="20" height="14" rx="1.5" fill="#e9a43a"/><path d="M3 6.5l9 6.5 9-6.5" fill="none" stroke="#0c0c0d" stroke-width="1.6"/></svg>
        hello@crewlinehealth.com
      </li>
      <li>
        <svg class="contact-icon" viewBox="0 0 24 24" aria-hidden="true"><g fill="none" stroke="#e9a43a" stroke-width="2"><circle cx="12" cy="12" r="9.5"/><ellipse cx="12" cy="12" rx="4" ry="9.5"/><path d="M2.5 12h19M4 7h16M4 17h16"/></g></svg>
        <span>www.<span class="web-highlight">crewlinehealth</span>.com</span>
      </li>
    </ul>
  </div>
</section>

<section class="card card--back" aria-label="Business card back">
  <span class="brand-dot"></span>
  <span class="brand-name">CREWLINE HEALTH</span>
</section>

</body>
</html>
```